Bright Path Mentors Needs A New Website Design

We need a 8 page website designed for "Bright Path Mentors .ca" similar in design to: "keystone learning hub .com".

The winner/successful candidate on the home page will be asked to complete the following inner pages to complete the project:

About Us
Philosophy
How We Work
Work With Us
Blog
Find A Tutor
Contact

Target Market(s)

Tutoring business clients/children

Industry/Entity Type

Education

Number of Pages Required

5+ page

Font styles to use
Sans Serif

Requirements
Must have
• The attached logo included of course. Similar design to the design provided above in the brief. Clear high quality high resolution images of children in school settings.

```html
<!DOCTYPE html>
<html lang="en">
<head>
<meta charset="utf-8">
<title>Bright Path Mentors</title>
<link href="https://fonts.googleapis.com/css2?family=Roboto:wght@400;500;700&family=Roboto+Slab:wght@400;700&family=Raleway:wght@400;500;600&family=Playball&family=Crimson+Text:ital@1&display=swap" rel="stylesheet">
<style>
:root{
  --blue:#2b3590;
  --blue-deep:#232b7e;
  --orange:#f7941d;
  --white:#ffffff;
  --grey-bg:#ececec;
  --text:#555a66;
  --line:#d9d9d9;
}
*{box-sizing:border-box;margin:0;padding:0}
html,body{width:1200px;height:2985px;overflow:hidden}
body{position:relative;background:var(--white);font-family:'Raleway',sans-serif;color:var(--text)}
.band{position:absolute;left:0;width:1200px}

/* top bar */
.topbar{top:0;height:44px;background:#ffc56b}
.socials{position:absolute;right:98px;top:6px;display:flex;gap:8px}
.socials span{width:32px;height:32px;border:2px solid #333;border-radius:50%;display:block}

/* nav */
.navbar{top:44px;height:92px;background:var(--blue)}
.brand-badge{position:absolute;left:100px;top:2px;width:172px;height:172px;border-radius:50%;background:var(--white);z-index:5;display:flex;align-items:center;justify-content:center;text-align:center;font-family:'Roboto',sans-serif;font-weight:700;font-size:22px;line-height:1.15;color:var(--blue);padding:20px}
.nav-links{position:absolute;left:336px;top:36px;display:flex;gap:19px;font-family:'Roboto',sans-serif;font-size:14.5px;color:var(--white);text-transform:uppercase}

/* hero */
.hero{top:136px;height:550px;background:linear-gradient(115deg,#6f7a88 0%,#a59a8a 40%,#c9a88a 65%,#7a6a5c 100%)}
.hero-text{position:absolute;left:98px;top:124px;color:var(--white);font-family:'Roboto',sans-serif}
.hero-text .kicker{font-size:24px;font-weight:500}
.hero-text h1{font-family:'Roboto Slab',serif;font-size:46px;font-weight:700;margin-top:8px}
.btn-outline{position:absolute;left:98px;top:250px;width:196px;height:48px;border:2px solid var(--white);border-radius:24px;color:var(--white);font-family:'Roboto',sans-serif;font-weight:500;font-size:16px;display:flex;align-items:center;justify-content:center}
.arrow{position:absolute;top:246px}
.feature-row{position:absolute;left:98px;top:380px;display:flex;gap:16px}
.feature{width:324px;height:128px;display:flex;align-items:center;padding-left:14px;color:var(--white);font-family:'Roboto',sans-serif}
.feature.blue{background:rgba(43,53,144,.88)}
.feature.orange{background:rgba(247,148,29,.92)}
.feature svg{flex:none;margin-right:18px}
.feature .title{font-size:19px;font-weight:700;line-height:1.45;text-transform:uppercase;padding-left:18px;border-left:1px solid rgba(255,255,255,.7)}
.feature .sub{font-size:15px;margin-top:8px;font-weight:500;padding-left:18px}

/* about */
.about{top:686px;height:380px}
.section-title{font-family:'Roboto',sans-serif;font-size:28px;font-weight:500;color:var(--blue);text-transform:uppercase}
.section-title em{font-style:normal;color:var(--orange)}
.about .section-title{position:absolute;left:98px;top:42px}
.about .underline{position:absolute;left:98px;top:86px;width:264px;height:2px;background:var(--blue)}
.about-copy{position:absolute;left:98px;top:104px;width:564px;font-size:12.5px;line-height:1.95}
.about-copy p+p{margin-top:8px}
.btn-pill{position:absolute;left:98px;top:300px;width:164px;height:40px;border-radius:20px;background:var(--blue);color:var(--white);font-family:'Roboto',sans-serif;font-weight:500;font-size:15px;display:flex;align-items:center;justify-content:center}
.video{position:absolute;left:698px;top:48px;width:404px;height:288px;background:linear-gradient(135deg,#dfe3ea,#c9d2de 55%,#e6c9a8);box-shadow:0 6px 14px rgba(0,0,0,.3)}
.video .play{position:absolute;left:174px;top:106px}
.video .controls{position:absolute;left:10px;right:10px;bottom:10px;height:20px;background:#2a2f3a}
.video .controls i{position:absolute;left:8px;top:8px;width:270px;height:4px;background:#4aa3df}

/* academic */
.academic{top:1066px;height:600px;background:var(--grey-bg)}
.academic .section-title{position:absolute;left:0;width:1200px;text-align:center;top:36px}
.academic .underline{position:absolute;left:450px;top:82px;width:300px;height:2px;background:var(--blue)}
.pager{position:absolute;left:1028px;top:58px;display:flex;gap:6px}
.pager span{width:30px;height:30px;border:1.5px solid #444;border-radius:50%;display:flex;align-items:center;justify-content:center}
.cards{position:absolute;left:98px;top:130px;display:flex;gap:46px}
.card{width:306px;height:420px;background:#f6f6f6;border:1px solid var(--line)}
.card .photo{height:218px}
.card h3{font-family:'Roboto',sans-serif;font-size:17px;font-weight:500;text-transform:uppercase;margin:22px 16px 8px}
.card.math h3{color:var(--blue)}
.card.science h3,.card.language h3{color:var(--orange)}
.card p{margin:0 16px;font-size:12.5px;line-height:1.85;text-align:justify}
.card .btn{display:flex;align-items:center;justify-content:center;margin:20px 16px 0;width:106px;height:42px;color:var(--white);font-family:'Roboto',sans-serif;font-size:14px;font-weight:500}
.card.math .btn{background:var(--blue)}
.card.science .btn,.card.language .btn{background:var(--orange)}

/* why */
.why{top:1666px;height:534px;background:linear-gradient(180deg,#2d3795 0%,#3640a2 50%,#2a3290 100%)}
.why h2{position:absolute;left:0;width:1200px;top:40px;text-align:center;font-family:'Roboto',sans-serif;font-size:28px;font-weight:700;color:var(--white)}
.why .underline{position:absolute;left:508px;top:90px;width:184px;height:2px;background:var(--white)}
.point{position:absolute;width:250px;color:var(--white)}
.point h4{font-family:'Roboto Slab',serif;font-weight:400;font-size:23px;margin-bottom:12px}
.point p{font-size:12px;line-height:1.75}
.point.left{text-align:right;left:94px}
.point.right{left:866px}
.icon-dot{position:absolute;width:68px;height:68px;border-radius:50%;background:var(--orange);display:flex;align-items:center;justify-content:center}
.shield{position:absolute;left:442px;top:148px}
.shield-copy{position:absolute;left:462px;top:200px;width:280px;text-align:center}
.shield-copy h3{font-family:'Playball',cursive;font-weight:400;font-size:28px;color:var(--blue);line-height:1.2}
.shield-copy p{font-size:12.5px;line-height:1.9;margin-top:12px;color:#555}
.shield-copy .btn{display:inline-flex;align-items:center;justify-content:center;margin-top:14px;width:104px;height:40px;background:var(--orange);color:var(--white);font-family:'Roboto',sans-serif;font-size:14px}

/* testimonials */
.testimonials{top:2200px;height:404px;background:#ededee}
.testimonials .section-title{position:absolute;left:0;width:1200px;text-align:center;top:52px}
.testimonials .section-title em{margin-left:8px}
.quote{position:absolute;left:0;width:1200px;top:152px;text-align:center;font-family:'Crimson Text',serif;font-style:italic;font-size:21px;line-height:2;color:var(--orange)}
.qmark{position:absolute;font-family:'Roboto Slab',serif;font-weight:700;font-size:72px;color:var(--blue);line-height:1}
.author{position:absolute;left:0;width:1200px;top:254px;text-align:center;font-family:'Roboto',sans-serif;font-size:16px;color:#222}
.author small{font-size:11px}
.btn-testi{position:absolute;left:492px;top:302px;width:222px;height:46px;border-radius:23px;background:var(--blue);color:var(--white);font-family:'Roboto',sans-serif;font-size:16px;font-weight:500;display:flex;align-items:center;justify-content:center}

/* footer */
.footer{top:2604px;height:336px;background:var(--blue);color:var(--white)}
.footer-brand{position:absolute;left:98px;top:120px;width:200px;text-align:center;font-family:'Roboto',sans-serif;font-weight:700;font-size:28px;line-height:1.2}
.footer h5{position:absolute;top:42px;font-family:'Roboto',sans-serif;font-size:16px;font-weight:700;text-transform:uppercase;padding-bottom:6px;border-bottom:2px solid var(--white)}
.links{position:absolute;left:404px;top:98px;list-style:none;font-size:13.5px;line-height:32px}
.contact-item{position:absolute;left:580px;display:flex;gap:18px;font-size:12.5px;line-height:1.6}
.contact-item b{font-family:'Roboto',sans-serif;font-size:14px}
.ring{flex:none;width:40px;height:40px;border:2px solid var(--white);border-radius:50%;display:flex;align-items:center;justify-content:center}
.field{position:absolute;border:1px solid rgba(255,255,255,.8);font-size:10px;padding:8px 10px}
.send{position:absolute;left:818px;top:218px;width:118px;height:38px;background:var(--orange);font-size:11px;display:flex;align-items:center;justify-content:center;text-transform:uppercase}

/* bottom */
.bottombar{top:2940px;height:45px;background:var(--orange);color:var(--white);font-size:12.5px}
.bottombar .copy{position:absolute;left:98px;top:14px}
.bottombar .socials{top:6px;right:92px}
.bottombar .socials span{border-color:var(--white)}
.bottombar .ver{position:absolute;right:34px;top:14px}
</style>
</head>
<body>

<header>
  <div class="band topbar">
    <div class="socials"><span></span><span></span><span></span><span></span><span></span></div>
  </div>
  <div class="brand-badge">Bright Path Mentors</div>
  <nav class="band navbar">
    <div class="nav-links">
      <span>Home</span><span>About Us</span><span>Philosophy</span><span>How We Work</span><span>Work With Us</span><span>Blog</span><span>Find A Tutor</span><span>Contact</span>
    </div>
  </nav>
</header>

<section class="band hero" role="img" aria-label="Classroom photo of a smiling boy raising his hand among classmates">
  <div class="hero-text">
    <div class="kicker">BETTER EDUCATION FOR A</div>
    <h1>BETTER WORLD</h1>
  </div>
  <div class="btn-outline">LEARN WITH US</div>
  <svg class="arrow" style="left:24px" width="24" height="56" viewBox="0 0 24 56"><path d="M20 4 4 28l16 24" fill="none" stroke="#fff" stroke-width="2"/></svg>
  <svg class="arrow" style="right:16px" width="24" height="56" viewBox="0 0 24 56"><path d="M4 4l16 24L4 52" fill="none" stroke="#fff" stroke-width="2"/></svg>
  <div class="feature-row">
    <div class="feature blue">
      <svg width="56" height="44" viewBox="0 0 56 44"><path d="M28 4 2 16l26 12 26-12z" fill="#fff"/><path d="M12 22v12c8 6 24 6 32 0V22L28 30z" fill="#fff"/><path d="M50 18v16" stroke="#fff" stroke-width="2"/></svg>
      <div><div class="title">Making Parents &amp;<br>Kids Happy</div><div class="sub">Our Reviews</div></div>
    </div>
    <div class="feature orange">
      <svg width="56" height="44" viewBox="0 0 56 44" fill="none" stroke="#fff" stroke-width="3"><rect x="20" y="4" width="32" height="22"/><circle cx="10" cy="16" r="5"/><path d="M2 40V28h16l8-8"/><path d="M26 34h8m4 0h8"/></svg>
      <div><div class="title">Tutoring With A<br>Personal Touch</div><div class="sub">How We Work</div></div>
    </div>
    <div class="feature blue">
      <svg width="56" height="44" viewBox="0 0 56 44" fill="none" stroke="#fff" stroke-width="3"><path d="M8 4h34v24"/><path d="M8 4v36h22"/><path d="M16 14h18M16 22h18"/><circle cx="40" cy="32" r="6"/><path d="M36 37l-2 6 6-3 6 3-2-6"/></svg>
      <div><div class="title">Satisfaction<br>Guranteed</div><div class="sub">Find Your Tutor</div></div>
    </div>
  </div>
</section>

<section class="band about">
  <h2 class="section-title">About <em>BrightPathMentors</em></h2>
  <div class="underline"></div>
  <div class="about-copy">
    <p>Maren found her passion for teaching as a high school student. She spent her summer and evenings tutoring the students in her neighborhood. Watching her students grow and succeed by giving them encouragement and specific strategies is what fostered her love of learning. Maren went on to complete.</p>
    <p>After graduating from her Masters in Education from the University of Eastbrook she moved back to Toronto and began working along side a tutoring agency in charge of running a region in the GTA.</p>
  </div>
  <div class="btn-pill">START CHATTING</div>
  <div class="video" role="img" aria-label="Video still of an illustrated teacher with young students">
    <svg class="play" width="56" height="56" viewBox="0 0 56 56"><circle cx="28" cy="28" r="26" fill="rgba(40,40,50,.55)" stroke="#fff" stroke-width="2"/><path d="M22 17l17 11-17 11z" fill="#fff"/></svg>
    <div class="controls"><i></i></div>
  </div>
</section>

<section class="band academic">
  <h2 class="section-title">Academic <em>Tutoring</em></h2>
  <div class="underline"></div>
  <div class="pager">
    <span><svg width="10" height="12" viewBox="0 0 10 12"><path d="M7 1 2 6l5 5" fill="none" stroke="#333" stroke-width="2"/></svg></span>
    <span><svg width="10" height="12" viewBox="0 0 10 12"><path d="M3 1l5 5-5 5" fill="none" stroke="#333" stroke-width="2"/></svg></span>
  </div>
  <div class="cards">
    <article class="card math">
      <div class="photo" role="img" aria-label="Photo of a parent helping a child with math homework" style="background:linear-gradient(135deg,#6b4a3a,#c9a36a 60%,#e9e2d6)"></div>
      <h3>Math Tutoring</h3>
      <p>One of Bright Path Mentors highly accredited tutors will work one-on-one with students as young as pre-kindergarten.</p>
      <div class="btn">Read More</div>
    </article>
    <article class="card science">
      <div class="photo" role="img" aria-label="Photo of a girl writing in a notebook with science sketches behind her" style="background:linear-gradient(135deg,#e8e8ea,#d9c36a 55%,#f1ecd9)"></div>
      <h3>Science Tutoring</h3>
      <p>One of Bright Path Mentors highly accredited tutors will work one-on-one with students as young as pre-kindergarten.</p>
      <div class="btn">Read More</div>
    </article>
    <article class="card language">
      <div class="photo" role="img" aria-label="Photo of two smiling girls at a classroom desk" style="background:linear-gradient(135deg,#4a5560,#d8a9b0 50%,#ece6dd)"></div>
      <h3>Foreign Language</h3>
      <p>One of Bright Path Mentors highly accredited tutors will work one-on-one with students as young as pre-kindergarten.</p>
      <div class="btn">Read More</div>
    </article>
  </div>
</section>

<section class="band why" role="img" aria-label="Faint classroom photo under a blue overlay">
  <h2>WHY BRIGHTPATH MENTORS?</h2>
  <div class="underline"></div>

  <div class="point left" style="top:190px"><h4>Certified Teachers</h4><p>After graduating from her Masters in Education from the University of Eastbrook she moved back to Toronto</p></div>
  <div class="point left" style="top:328px"><h4>Flexible In Tutoring</h4><p>After graduating from her Masters in Education from the University of Eastbrook she moved back to Toronto</p></div>
  <div class="point right" style="top:190px"><h4>Personal Attention</h4><p>After graduating from her Masters in Education from the University of Eastbrook she moved back to Toronto</p></div>
  <div class="point right" style="top:328px"><h4>Tutor Gurantee</h4><p>After graduating from her Masters in Education from the University of Eastbrook she moved back to Toronto</p></div>

  <div class="icon-dot" style="left:360px;top:192px"><svg width="34" height="30" viewBox="0 0 34 30" fill="none" stroke="#fff" stroke-width="2.5"><rect x="12" y="2" width="20" height="14"/><circle cx="6" cy="10" r="3.5"/><path d="M1 28V19h10l5-5"/></svg></div>
  <div class="icon-dot" style="left:360px;top:328px"><svg width="30" height="34" viewBox="0 0 30 34" fill="#fff"><circle cx="15" cy="9" r="7"/><path d="M3 34c0-10 5-14 12-14s12 4 12 14z"/></svg></div>
  <div class="icon-dot" style="left:780px;top:192px"><svg width="30" height="34" viewBox="0 0 30 34" fill="#fff"><circle cx="15" cy="8" r="6"/><path d="M4 32V22c0-5 4-8 11-8s11 3 11 8v10z"/><rect x="9" y="22" width="12" height="8" fill="#f7941d"/></svg></div>
  <div class="icon-dot" style="left:780px;top:328px"><svg width="32" height="30" viewBox="0 0 32 30" fill="#fff"><rect x="2" y="12" width="6" height="16"/><path d="M10 12l7-10c3 0 4 2 3 6l-1 4h9c2 0 3 2 2 4l-4 10c-1 2-2 2-4 2H10z"/></svg></div>

  <svg class="shield" width="320" height="324" viewBox="0 0 320 324"><path d="M160 4 C110 26 56 30 8 22 V150 C8 236 80 292 160 320 C240 292 312 236 312 150 V22 C264 30 210 26 160 4Z" fill="#fff" stroke="#2b3590" stroke-width="4"/><path d="M160 14 C112 34 62 38 18 32 V150 C18 228 86 280 160 308 C234 280 302 228 302 150 V32 C258 38 208 34 160 14Z" fill="none" stroke="#2b3590" stroke-width="1.5"/></svg>
  <div class="shield-copy">
    <h3>Highly Credentialed<br>Tutors</h3>
    <p>We require the most rigorous qualifications of our tutors, in addition to a background check.</p>
    <span class="btn">Read More</span>
  </div>
</section>

<section class="band testimonials">
  <h2 class="section-title">Read Our <em>Testimonials</em></h2>
  <span class="qmark" style="left:168px;top:134px">&ldquo;</span>
  <p class="quote">Maren Delacroix Dear Ms. Delacroix: RE: Highest Recommendation for Tutoring Services<br>I take this opportunity to give the highest...</p>
  <span class="qmark" style="left:952px;top:198px">&rdquo;</span>
  <p class="author">Nora P. <small>(VAUGHAN, ONTARIO)</small></p>
  <div class="btn-testi">Read More Testimonials</div>
</section>

<footer class="band footer">
  <div class="footer-brand">Bright Path Mentors</div>

  <h5 style="left:404px">Quick Links</h5>
  <ul class="links">
    <li>&rsaquo; Home</li><li>&rsaquo; About Us</li><li>&rsaquo; Philosophy</li><li>&rsaquo; How We Work</li><li>&rsaquo; Work With Us</li><li>&rsaquo; Contact Us</li>
  </ul>

  <h5 style="left:580px">Contact Us</h5>
  <div class="contact-item" style="top:98px">
    <span class="ring"><svg width="14" height="18" viewBox="0 0 14 18"><path d="M7 1a6 6 0 0 0-6 6c0 5 6 10 6 10s6-5 6-10a6 6 0 0 0-6-6z" fill="#fff"/><circle cx="7" cy="7" r="2.2" fill="#2b3590"/></svg></span>
    <div><b>BRIGHTPATHMENTORS,</b><br>1820 Harbour Lane #210,<br>North York, ON M2N</div>
  </div>
  <div class="contact-item" style="top:176px">
    <span class="ring"><svg width="12" height="18" viewBox="0 0 12 18"><rect x="1" y="1" width="10" height="16" rx="2" fill="none" stroke="#fff" stroke-width="2"/><circle cx="6" cy="14" r="1" fill="#fff"/></svg></span>
    <div><b>PHONE:</b><br>1-855-555-0142</div>
  </div>
  <div class="contact-item" style="top:238px">
    <span class="ring"><svg width="18" height="14" viewBox="0 0 18 14"><rect x="1" y="1" width="16" height="12" fill="#fff"/><path d="M1 1l8 7 8-7" fill="none" stroke="#2b3590" stroke-width="1.5"/></svg></span>
    <div><b>Mail:</b><br>info@brightpathmentors.ca</div>
  </div>

  <h5 style="left:818px">Contact Form</h5>
  <div class="field" style="left:818px;top:92px;width:138px;height:38px">Name</div>
  <div class="field" style="left:966px;top:92px;width:140px;height:38px">Phone</div>
  <div class="field" style="left:818px;top:136px;width:288px;height:66px">Message</div>
  <div class="send">Send Message</div>
</footer>

<div class="band bottombar">
  <span class="copy">Copyright &copy; 2016 Bright Path Mentors. All Right Reserved</span>
  <div class="socials"><span></span><span></span><span></span><span></span></div>
  <span class="ver">c 20</span>
</div>

</body>
</html>
```